New Business Card Design for Manufacturing

We are an engineering/manufacturing company that offers Advanced machining/assembly/engineering services, as well as innovative products for the heavy duty engine cooling markets.

We are looking to get a new business card designed that is clean and modern looking, but still fits the wide range of technical/skilled work we do.

- We hope to use this design as the base for other design work in new Presentations, web, and print work.

Industry/Entity Type

Engineering

Contact Information for Business Card

Our preferred color of blue is (RGB) 22/71/159 but can vary slightly from that color. Our content will be our Logo and full company name (Vantrell Forge Works, Inc.), company address, name, job title, phone number with extension, cell number, fax number, website, and email address on the cards.
We'd like the full company name next to the logo, but we are open to other interpretations of that layout.
Preferably, we would like the back side to be clean with just our logo, and the front to contain all of the contact information.

Colors
2f74b4
0355a3
85abd2

Requirements
Must have
• - Logo, company name, needed content - We are open to interpretation beyond that.
• - Standard size business card.
• - Horizontal orientation.
• - Enough space for lengthy names / job titles (for example, a job title could read "Directory of Human Resources" or "V.P. of Governmental Affairs"). We need this to look clean, whether the title be short (CEO) or long (as described above).

```html
<!DOCTYPE html>
<html lang="en">
<head>
<meta charset="utf-8">
<title>Vantrell Forge Works – Business Card</title>
<link rel="stylesheet" href="https://fonts.googleapis.com/css2?family=Open+Sans:wght@400;600;700;800&display=swap">
<style>
  :root {
    --brand-blue: #16479f;
    --brand-blue-deep: #123c88;
    --brand-blue-light: #2f74b4;
    --ink-grey: #6d6e70;
    --rule-grey: #b9bbbe;
    --band-grey: #c9cbce;
    --card-white: #ffffff;
    --stage: #e6e7e9;
  }
  * { margin: 0; padding: 0; box-sizing: border-box; }
  html, body { width: 1200px; height: 862px; overflow: hidden; }
  body {
    background: var(--stage);
    font-family: "Open Sans", Arial, sans-serif;
    position: relative;
  }
  .card {
    position: absolute;
    width: 560px;
    height: 320px;
    overflow: hidden;
    box-shadow: 0 6px 18px rgba(0,0,0,0.18);
  }

  /* Back side */
  .card-back {
    left: 90px; top: 70px;
    background: var(--brand-blue);
  }
  .card-back .wordmark {
    position: absolute;
    left: 0; right: 0; top: 104px;
    text-align: center;
    font-weight: 800;
    font-size: 58px;
    letter-spacing: 2px;
    color: var(--brand-blue-deep);
    line-height: 1;
  }
  .card-back .tagline {
    position: absolute;
    left: 0; right: 0; top: 172px;
    text-align: center;
    font-weight: 700;
    font-size: 15px;
    letter-spacing: 1px;
    color: var(--brand-blue-deep);
  }
  .card-back .web {
    position: absolute;
    left: 0; right: 0; bottom: 34px;
    text-align: center;
    font-size: 11px;
    color: var(--brand-blue-deep);
  }

  /* Front side */
  .card-front {
    left: 550px; top: 460px;
    background: var(--card-white);
  }
  .front-wordmark {
    position: absolute;
    left: 30px; top: 92px;
    font-weight: 800;
    font-size: 46px;
    letter-spacing: 1px;
    color: var(--brand-blue);
    line-height: 1;
  }
  .front-tagline {
    position: absolute;
    left: 32px; top: 146px;
    font-weight: 700;
    font-size: 15px;
    letter-spacing: 0.5px;
    color: var(--ink-grey);
  }
  .company-name {
    position: absolute;
    left: 318px; top: 30px;
    font-weight: 800;
    font-size: 17px;
    line-height: 1.05;
    color: var(--brand-blue);
    text-transform: uppercase;
  }
  .company-name .suffix { font-size: 8px; font-weight: 700; vertical-align: top; margin-left: 3px; }
  .person {
    position: absolute;
    right: 40px; top: 102px;
    text-align: right;
  }
  .person .name { font-weight: 700; font-size: 17px; color: var(--brand-blue); line-height: 1.1; }
  .person .title { font-size: 9px; color: var(--ink-grey); }
  .rule-top {
    position: absolute;
    left: 300px; right: 40px; top: 142px;
    border-top: 1px solid var(--rule-grey);
  }
  .address {
    position: absolute;
    right: 40px; top: 168px;
    font-size: 9.5px;
    color: var(--ink-grey);
    line-height: 1.45;
  }
  .address li { list-style: none; display: flex; align-items: center; gap: 6px; }
  .address li.web { color: var(--brand-blue-light); }
  .address svg { width: 10px; height: 10px; fill: var(--brand-blue); }
  .rule-contact {
    position: absolute;
    left: 30px; width: 190px; top: 212px;
    border-top: 1px solid var(--rule-grey);
  }
  .contacts {
    position: absolute;
    left: 30px; top: 220px;
    font-size: 10px;
    color: var(--ink-grey);
    line-height: 1.55;
  }
  .contacts li { list-style: none; display: flex; align-items: center; gap: 8px; }
  .contacts svg { width: 10px; height: 10px; fill: var(--brand-blue); }
  .bands { position: absolute; left: 0; bottom: 0; width: 560px; height: 40px; }
</style>
</head>
<body>

<section class="card card-back" aria-label="Card back">
  <div class="wordmark">VANTRELL</div>
  <div class="tagline">SHAPING WHAT RUNS</div>
  <div class="web">www.yourmailaddress.com</div>
</section>

<section class="card card-front" aria-label="Card front">
  <div class="front-wordmark">VANTRELL</div>
  <div class="front-tagline">SHAPING WHAT RUNS</div>

  <div class="company-name">Vantrell<br>Forge<br>Works<span class="suffix">INC</span></div>

  <div class="person">
    <div class="name">Marcus Hale</div>
    <div class="title">President</div>
  </div>
  <div class="rule-top"></div>

  <ul class="address">
    <li><span style="width:10px"></span>Street Name Avenue, Suite 100</li>
    <li><svg viewBox="0 0 10 10"><path d="M5 0a3.5 3.5 0 0 0-3.5 3.5C1.5 6 5 10 5 10s3.5-4 3.5-6.5A3.5 3.5 0 0 0 5 0zm0 5a1.4 1.4 0 1 1 0-2.8A1.4 1.4 0 0 1 5 5z"/></svg>State, Zip Code, Country</li>
    <li class="web"><svg viewBox="0 0 10 10"><circle cx="5" cy="5" r="4.3" fill="none" stroke="#16479f" stroke-width="1"/><path d="M0.7 5h8.6M5 0.7c-2 2.4-2 6.2 0 8.6M5 0.7c2 2.4 2 6.2 0 8.6" fill="none" stroke="#16479f" stroke-width="0.8"/></svg>www.yourmailaddress.com</li>
  </ul>

  <div class="rule-contact"></div>
  <ul class="contacts">
    <li><svg viewBox="0 0 10 10"><path d="M2 0.5l2 2-1 1.2c.6 1.3 1.6 2.3 2.9 2.9l1.2-1 2 2-1.3 1.8C4.5 9.2 0.8 5.5.5 1.8z"/></svg>+000.000.00 00</li>
    <li><svg viewBox="0 0 10 10"><rect x="2.5" y="0.5" width="5" height="9" rx="1"/><rect x="3.3" y="1.5" width="3.4" height="6" fill="#fff"/></svg>+000.000.00 00</li>
    <li><svg viewBox="0 0 10 10"><rect x="2.5" y="0.5" width="5" height="3"/><rect x="0.5" y="3.5" width="9" height="4" rx="0.8"/><rect x="2.5" y="6.5" width="5" height="3"/></svg>+000.000.00 00</li>
    <li><svg viewBox="0 0 10 10"><rect x="0.5" y="1.8" width="9" height="6.4"/><path d="M0.8 2.2L5 5.6l4.2-3.4" fill="none" stroke="#fff" stroke-width="0.9"/></svg>www.yourmailaddress.com</li>
  </ul>

  <svg class="bands" viewBox="0 0 560 40" aria-hidden="true">
    <polygon points="0,40 0,33 330,33 350,14 560,14 560,40" fill="#ffffff"/>
    <polygon points="0,33 340,33 355,20 372,20 348,40 0,40" fill="#16479f"/>
    <polygon points="372,20 560,20 560,14 378,14" fill="#c9cbce"/>
    <polygon points="0,40 0,36 345,36 372,14 560,14 560,11 370,11 344,33 0,33" fill="#16479f" opacity="0"/>
  </svg>
</section>

</body>
</html>
```